SkyvornQ Business Cards and Stationary Design

Need a design for our business cards and stationary. I want to carry on the theme of the logo. I want the business cards to have a design on the back. I would like the business cards and the stationary to carry the same theme, design scheme, and branding

Target Market(s)

Airlines and Maintenance Facilities

Industry/Entity Type

Aviation

Contact Information for Business Card

Name
Position Title
Address: 4827 Trellis Hollow Road, Fort Pierce, Florida, 34951
Office Number
Mobile Number
Email
Website

Font styles to use
Serif
Sans Serif

Colors

Designer to choose colors to be used in the design.

```html
<!DOCTYPE html>
<html lang="en">
<head>
<meta charset="utf-8">
<title>SkyvornQ Business Card</title>
<link href="https://fonts.googleapis.com/css2?family=Montserrat:wght@700&family=Open+Sans:wght@400;700&display=swap" rel="stylesheet">
<style>
  :root {
    --backdrop: #3a3b3e;
    --card: #1f2024;
    --navy: #162a5c;
    --sky: #1ea7ec;
    --stripe: #3b3d43;
    --emboss: #6f7176;
    --white: #ffffff;
    --soft: #d9dbe0;
  }
  * { margin: 0; padding: 0; box-sizing: border-box; }
  html, body {
    width: 799px; height: 1200px; overflow: hidden;
    background: var(--backdrop);
  }
  .sheet { position: relative; width: 799px; height: 1200px; }
  .card {
    position: absolute; left: 90px; width: 620px; height: 354px;
    border-radius: 24px; overflow: hidden; background: var(--card);
  }
  .card-front { top: 140px; }
  .card-back { top: 706px; }

  .front-brand {
    position: absolute; inset: 0;
    display: flex; flex-direction: column; align-items: center; justify-content: center; gap: 18px;
  }
  .brand-dot { width: 74px; height: 74px; border-radius: 50%; background: var(--emboss); }
  .brand-name {
    font-family: "Montserrat", sans-serif; font-weight: 700;
    letter-spacing: 6px; line-height: 1;
  }
  .front-brand .brand-name { font-size: 46px; color: var(--emboss); }

  .back-art { position: absolute; inset: 0; }

  .back-brand {
    position: absolute; left: 48px; top: 62px;
    display: flex; flex-direction: column; align-items: flex-start; gap: 14px;
  }
  .back-brand .brand-dot { width: 70px; height: 70px; margin-left: 62px; background: #1a8fd6; }
  .back-brand .brand-name { font-size: 32px; color: var(--white); letter-spacing: 4px; }

  .address {
    position: absolute; left: 48px; top: 208px;
    font-family: "Open Sans", sans-serif; font-style: normal;
    font-size: 14px; line-height: 1.35; color: var(--soft);
  }
  .holder {
    position: absolute; right: 30px; top: 94px; text-align: right;
    font-family: "Open Sans", sans-serif; color: var(--white);
  }
  .holder-name { font-size: 23px; font-weight: 700; line-height: 1.1; }
  .holder-role { font-size: 13px; margin-top: 4px; color: var(--soft); }

  .contacts {
    position: absolute; right: 28px; bottom: 24px; list-style: none;
    font-family: "Open Sans", sans-serif; font-size: 14px; color: var(--soft);
  }
  .contacts li {
    display: flex; justify-content: flex-end; align-items: center; gap: 8px; line-height: 22px;
  }
  .contacts svg { width: 14px; height: 14px; fill: var(--sky); }
</style>
</head>
<body>
<main class="sheet">

  <section class="card card-front" aria-label="Card front">
    <div class="front-brand">
      <span class="brand-dot"></span>
      <span class="brand-name">SKYVORNQ</span>
    </div>
  </section>

  <section class="card card-back" aria-label="Card back">
    <svg class="back-art" viewBox="0 0 620 354" preserveAspectRatio="none" aria-hidden="true">
      <path d="M0,0 H620 V212 C530,205 440,178 385,118 C330,58 250,12 0,16 Z" fill="var(--navy)"/>
      <path d="M0,44 C250,36 320,80 372,136 C425,196 520,226 620,232" fill="none" stroke="var(--stripe)" stroke-width="16"/>
      <path d="M0,24 C250,16 330,62 380,122 C432,184 525,214 620,222" fill="none" stroke="var(--sky)" stroke-width="8"/>
    </svg>

    <div class="back-brand">
      <span class="brand-dot"></span>
      <span class="brand-name">SKYVORNQ</span>
    </div>

    <address class="address">4827 Trellis Hollow Road,<br>Corwin Bay, Florida, 34951</address>

    <div class="holder">
      <p class="holder-name">Marcus Delvane</p>
      <p class="holder-role">Managing Director</p>
    </div>

    <ul class="contacts">
      <li>4410 2276 315
        <svg viewBox="0 0 16 16"><path d="M3 1h3l1 4-2 1c1 2 3 4 5 5l1-2 4 1v3c0 1-1 2-2 2C7 15 1 9 1 3c0-1 1-2 2-2z"/></svg></li>
      <li>4410 2276 842
        <svg viewBox="0 0 16 16"><path d="M4 0h8a1 1 0 0 1 1 1v14a1 1 0 0 1-1 1H4a1 1 0 0 1-1-1V1a1 1 0 0 1 1-1zm1 2v10h6V2zm3 11a1 1 0 1 0 0 2 1 1 0 0 0 0-2z"/></svg></li>
      <li>marcus@skyvornq.com
        <svg viewBox="0 0 16 16"><path d="M0 3h16v10H0zm1 1v.5l7 5 7-5V4z"/></svg></li>
      <li>www.skyvornq.com
        <svg viewBox="0 0 16 16"><path d="M8 0a8 8 0 1 0 0 16A8 8 0 0 0 8 0zm-1 2c-1 1-2 3-2 5H2a6 6 0 0 1 5-5zm2 0a6 6 0 0 1 5 5h-3c0-2-1-4-2-5zM6 7c0-2 1-4 2-5 1 1 2 3 2 5zm-4 2h3c0 2 1 4 2 5a6 6 0 0 1-5-5zm4 0h4c0 2-1 4-2 5-1-1-2-3-2-5zm5 0h3a6 6 0 0 1-5 5c1-1 2-3 2-5z"/></svg></li>
    </ul>
  </section>

</main>
</body>
</html>
```